1 Page for Computer Repair Website

Looking for a 1 page website with a design that compliments the business card and pamphlet that have already been made (attached files). It should look business professional and easy to read. Email and phone number should be somewhere near the top of the website, visible when the page loads. I don't want any forms for people to mess with. No "Contact Us" form or entering in email for newsletter. Customers will just be looking at this site to confirm we are professionals and have our business in order.

Target Market(s)

Home and small business

Industry/Entity Type

Computer Repair

Coding

Coded - Design and coding required

Number of Pages Required

1 page

Font styles to use
Other font styles liked:
• Helvetica variations used in pamphlet and card

Colors
0455a3
cfdeed
85abd2
3276b5
85cae6
ffffff

Requirements
Must have
• Compliment the pamphlet and business card in color choices and font use. Pleasing to the eye and easy to read through categories and text.
Should not have
• Forms. No "enter name and email here" or anything of the sort.

```html
<!DOCTYPE html>
<html lang="en">
<head>
<meta charset="utf-8">
<title>Keypoint Computer Services</title>
<link href="https://fonts.googleapis.com/css2?family=Lato:wght@400;700;900&display=swap" rel="stylesheet">
<style>
:root{
  --navy:#0b2d66;
  --navy-deep:#082250;
  --blue:#0455a3;
  --blue-mid:#3276b5;
  --sky:#85cae6;
  --soft:#cfdeed;
  --steel:#85abd2;
  --grey-bg:#f1f2f4;
  --text:#4a4f57;
  --muted:#8a9099;
  --white:#ffffff;
}
*{margin:0;padding:0;box-sizing:border-box}
html,body{width:1200px;height:3248px;overflow:hidden}
body{font-family:"Lato",Helvetica,Arial,sans-serif;color:var(--text);background:var(--white);position:relative}
section,header,footer{position:absolute;left:0;width:1200px}
.abs{position:absolute}
.btn{display:inline-block;background:var(--blue);color:var(--white);font-size:13px;font-weight:700;letter-spacing:.5px;padding:12px 22px;text-decoration:none}

/* header */
.site-header{top:0;height:112px;background:var(--white)}
.brand{left:72px;top:26px;color:var(--navy);font-weight:900;font-size:40px;line-height:40px;letter-spacing:1px}
.brand small{display:block;font-size:18px;font-weight:900;letter-spacing:0;line-height:22px}
.contact-item{top:42px;display:flex;align-items:center;gap:10px;font-size:15px;color:var(--text)}
.contact-item .ico{width:30px;height:30px;border-radius:50%;background:var(--soft);display:flex;align-items:center;justify-content:center}
.socials{right:72px;top:44px;display:flex;gap:10px}
.socials span{width:26px;height:26px;border-radius:50%;border:1px solid var(--steel);display:block}

/* hero */
.hero{top:112px;height:628px;overflow:hidden}
.hero-photo{left:0;top:0;width:1200px;height:628px;background:linear-gradient(120deg,#b9c6d4 0%,#8fa1b5 35%,#5d6f86 60%,#2f3a48 100%)}
.hero-wave{left:0;top:300px}
.hero-copy{left:58px;top:385px;color:var(--white)}
.hero-copy h1{font-size:40px;font-weight:700;line-height:48px}
.hero-copy h2{font-size:28px;font-weight:700;color:var(--sky);line-height:36px}
.hero-copy p{font-size:13px;width:420px;margin:14px 0 26px;line-height:19px;color:var(--soft)}
.hero-arrow{top:236px;width:36px;height:36px;border-radius:50%;background:var(--white);display:flex;align-items:center;justify-content:center}
.dots{left:906px;top:558px;display:flex;gap:8px}
.dots span{width:12px;height:12px;border-radius:50%;border:2px solid var(--white)}
.dots span.on{background:var(--white)}

/* welcome */
.welcome{top:740px;height:280px;text-align:center}
.section-title{font-size:26px;font-weight:900;color:var(--navy);letter-spacing:.5px}
.welcome .section-title{margin-top:50px}
.title-rule{width:60px;height:3px;background:var(--blue);margin:12px auto 0}
.welcome p{width:1080px;margin:22px auto 26px;font-size:13px;line-height:21px}
.welcome .btn{background:var(--navy)}

/* services */
.services{top:1020px;height:1180px;background:var(--grey-bg)}
.services .section-title{text-align:center;margin-top:50px;font-weight:400;color:#333}
.services .section-title b{color:var(--navy);font-weight:900}
.timeline{left:599px;top:128px;width:2px;height:1000px;background:#c9ced6}
.node{width:100px;height:100px;border-radius:50%;background:var(--navy);border:6px solid var(--white);box-shadow:0 0 0 1px #c9ced6;display:flex;align-items:center;justify-content:center}
.link{height:2px;background:#c9ced6}
.svc{width:330px}
.svc h3{font-size:18px;font-weight:700;color:#2a2f36;margin-bottom:8px}
.svc p{font-size:12.5px;line-height:19px}
.svc a{display:block;margin-top:10px;font-size:11px;font-weight:900;color:var(--navy);text-decoration:none}
.svc.left{text-align:right}
.svc.left h3{padding-right:0}

/* why */
.why{top:2200px;height:344px}
.why .section-title{text-align:center;margin-top:28px;font-size:36px;font-weight:400;color:#4a4f57}
.why .section-title b{color:var(--navy);font-weight:900}
.why-photo{left:48px;top:92px;width:472px;height:210px;background:linear-gradient(110deg,#3b5a86 0%,#9db4cf 45%,#e6ecf3 70%,#b8c7d9 100%)}
.why-list{left:580px;top:92px;width:580px;list-style:none}
.why-list li{position:relative;padding-left:20px;font-size:13px;line-height:19px;margin-bottom:12px}
.why-list li::before{content:"";position:absolute;left:0;top:6px;width:7px;height:7px;background:var(--navy)}

/* help */
.help{top:2544px;height:396px;background:var(--navy);color:var(--white);text-align:center}
.help h2{font-size:32px;font-weight:700;margin-top:48px}
.help-item{top:132px;width:240px;text-align:center}
.help-item .ring{width:100px;height:100px;border-radius:50%;border:3px solid var(--white);margin:0 auto;display:flex;align-items:center;justify-content:center;font-size:44px;font-weight:900}
.help-item span{display:block;margin-top:26px;font-size:18px;font-weight:900;letter-spacing:.5px}

/* footer */
.site-footer{top:2940px;height:240px;background:var(--white)}
.footer-brand{left:72px;top:50px;color:var(--navy);font-weight:900;font-size:64px;line-height:60px}
.footer-brand small{display:block;font-size:28px;line-height:34px}
.foot-col{top:54px;width:250px}
.foot-col h4{font-size:16px;font-weight:900;color:#2a2f36;margin-bottom:14px}
.foot-col ul{list-style:none}
.foot-col li{font-size:12.5px;line-height:24px;color:var(--muted);padding-left:14px;position:relative}
.foot-col li::before{content:"›";position:absolute;left:0;color:var(--blue)}
.bottom-bar{top:3180px;height:68px;background:var(--navy-deep);color:var(--soft);font-size:12px;display:flex;align-items:center;justify-content:center}
.bottom-social{right:40px;top:22px;display:flex;gap:8px}
.bottom-social span{width:24px;height:24px;background:var(--white);display:block}
</style>
</head>
<body>

<header class="site-header">
  <div class="abs brand">KEYPOINT<small>Computer Services</small></div>
  <div class="abs contact-item" style="left:440px">
    <span class="ico"><svg width="14" height="14" viewBox="0 0 24 24"><path fill="#0455a3" d="M6.6 10.8a15.1 15.1 0 0 0 6.6 6.6l2.2-2.2c.3-.3.7-.4 1-.2 1.1.4 2.3.6 3.6.6.6 0 1 .4 1 1V20c0 .6-.4 1-1 1A17 17 0 0 1 3 4c0-.6.4-1 1-1h3.5c.6 0 1 .4 1 1 0 1.3.2 2.5.6 3.6.1.3 0 .7-.2 1z"/></svg></span>
    555 014 2290
  </div>
  <div class="abs contact-item" style="left:640px">
    <span class="ico"><svg width="14" height="14" viewBox="0 0 24 24"><rect x="2" y="5" width="20" height="14" fill="none" stroke="#0455a3" stroke-width="2"/><path d="M2 5l10 8 10-8" fill="none" stroke="#0455a3" stroke-width="2"/></svg></span>
    hello@keypointpc.example
  </div>
  <div class="abs socials"><span></span><span></span><span></span><span></span><span></span></div>
</header>

<section class="hero">
  <div class="abs hero-photo" role="img" aria-label="Technician repairing the inside of a desktop computer tower"></div>
  <svg class="abs hero-wave" width="1200" height="328" viewBox="0 0 1200 328">
    <path d="M0 120 C300 40 600 160 900 90 C1020 60 1120 40 1200 50 L1200 328 L0 328Z" fill="#0b2d66"/>
    <path d="M0 95 C300 20 600 140 900 70 C1020 40 1120 20 1200 30" fill="none" stroke="#ffffff" stroke-width="10"/>
    <path d="M0 110 C300 35 600 152 900 82 C1020 52 1120 32 1200 42" fill="none" stroke="#3276b5" stroke-width="8"/>
  </svg>
  <div class="abs hero-arrow" style="left:12px"><svg width="14" height="14" viewBox="0 0 24 24"><path d="M15 4l-8 8 8 8" fill="none" stroke="#0b2d66" stroke-width="3"/></svg></div>
  <div class="abs hero-arrow" style="right:12px"><svg width="14" height="14" viewBox="0 0 24 24"><path d="M9 4l8 8-8 8" fill="none" stroke="#0b2d66" stroke-width="3"/></svg></div>
  <div class="abs hero-copy">
    <h1>Any Computer Problems?</h1>
    <h2>Receive Instant Service!</h2>
    <p>Fast, honest repair for home and small office computers, done right the first time.</p>
    <a class="btn" href="#">READ MORE</a>
  </div>
  <div class="abs dots"><span class="on"></span><span></span><span></span><span></span></div>
</section>

<section class="welcome">
  <h2 class="section-title">WELCOME TO KEYPOINT</h2>
  <div class="title-rule"></div>
  <p>We are a local team of certified technicians serving homes and small businesses. From a slow laptop to a failed office server, we diagnose the problem, explain the options in plain language and fix it quickly. Every job comes with clear pricing, careful handling of your data and a warranty on parts and labour, so you can get back to work with confidence and peace of mind.</p>
  <a class="btn" href="#">READ MORE</a>
</section>

<section class="services">
  <h2 class="section-title">OUR <b>SERVICE</b></h2>
  <div class="title-rule"></div>
  <div class="abs timeline"></div>

  <!-- right: hardware repair -->
  <div class="abs link" style="left:600px;top:249px;width:58px"></div>
  <div class="abs node" style="left:658px;top:200px"><svg width="36" height="36" viewBox="0 0 24 24"><rect x="2" y="4" width="20" height="13" rx="1" fill="none" stroke="#fff" stroke-width="2"/><path d="M8 21h8M12 17v4" stroke="#fff" stroke-width="2"/></svg></div>
  <div class="abs svc" style="left:784px;top:196px"><h3>PC/Laptop Hardware Repair</h3><p>Broken screens, failed drives, noisy fans and dead power supplies replaced with quality parts.</p><a href="#">READ MORE ›</a></div>

  <!-- left: malware -->
  <div class="abs link" style="left:542px;top:321px;width:58px"></div>
  <div class="abs node" style="left:442px;top:272px"><svg width="36" height="36" viewBox="0 0 24 24"><circle cx="12" cy="12" r="9" fill="none" stroke="#fff" stroke-width="2"/><path d="M12 6v12M6 12h12" stroke="#fff" stroke-width="2"/></svg></div>
  <div class="abs svc left" style="left:84px;top:268px"><h3>Malware Removal</h3><p>Thorough scans remove viruses, spyware and adware, then we harden your system against threats.</p><a href="#">READ MORE ›</a></div>

  <!-- right: data migration -->
  <div class="abs link" style="left:600px;top:417px;width:58px"></div>
  <div class="abs node" style="left:658px;top:368px"><svg width="36" height="36" viewBox="0 0 24 24"><rect x="3" y="4" width="7" height="16" fill="none" stroke="#fff" stroke-width="2"/><rect x="14" y="4" width="7" height="16" fill="none" stroke="#fff" stroke-width="2"/></svg></div>
  <div class="abs svc" style="left:784px;top:364px"><h3>Data Migration</h3><p>Move files, photos, email and settings safely from your old computer to a new one.</p><a href="#">READ MORE ›</a></div>

  <!-- left: upgrades -->
  <div class="abs link" style="left:542px;top:529px;width:58px"></div>
  <div class="abs node" style="left:442px;top:480px"><svg width="36" height="36" viewBox="0 0 24 24"><circle cx="12" cy="12" r="4" fill="none" stroke="#fff" stroke-width="2"/><path d="M12 2v4M12 18v4M2 12h4M18 12h4M5 5l3 3M16 16l3 3M19 5l-3 3M8 16l-3 3" stroke="#fff" stroke-width="2"/></svg></div>
  <div class="abs svc left" style="left:84px;top:476px"><h3>Hard/Software Upgrades</h3><p>More memory, faster storage and current software to give older machines new life.</p><a href="#">READ MORE ›</a></div>

  <!-- right: in-home -->
  <div class="abs link" style="left:600px;top:649px;width:58px"></div>
  <div class="abs node" style="left:658px;top:600px"><svg width="36" height="36" viewBox="0 0 24 24"><path d="M3 11l9-8 9 8M5 10v10h14V10" fill="none" stroke="#fff" stroke-width="2"/><rect x="10" y="14" width="4" height="6" fill="#fff"/></svg></div>
  <div class="abs svc" style="left:784px;top:596px"><h3>In-Home Installation</h3><p>We set up printers, networks and new computers at your home or office desk.</p><a href="#">READ MORE ›</a></div>

  <!-- left: data rescue -->
  <div class="abs link" style="left:542px;top:789px;width:58px"></div>
  <div class="abs node" style="left:442px;top:740px"><svg width="36" height="36" viewBox="0 0 24 24"><path d="M12 3l2.5 6.5L21 12l-6.5 2.5L12 21l-2.5-6.5L3 12l6.5-2.5z" fill="#fff"/></svg></div>
  <div class="abs svc left" style="left:84px;top:736px"><h3>Data Rescue</h3><p>Recover lost documents and photos from failing, damaged or accidentally erased drives.</p><a href="#">READ MORE ›</a></div>

  <!-- right: remote -->
  <div class="abs link" style="left:600px;top:901px;width:58px"></div>
  <div class="abs node" style="left:658px;top:852px"><svg width="36" height="36" viewBox="0 0 24 24"><path d="M13 2L5 14h6l-1 8 8-12h-6z" fill="#fff"/></svg></div>
  <div class="abs svc" style="left:784px;top:848px"><h3>Remote Support</h3><p>Quick fixes over a secure connection without waiting for a visit or a drop-off.</p><a href="#">READ MORE ›</a></div>

  <!-- left: tune ups -->
  <div class="abs link" style="left:542px;top:1013px;width:58px"></div>
  <div class="abs node" style="left:442px;top:964px"><svg width="36" height="36" viewBox="0 0 24 24"><circle cx="12" cy="12" r="9" fill="none" stroke="#fff" stroke-width="2"/><circle cx="12" cy="12" r="4" fill="none" stroke="#fff" stroke-width="2"/><path d="M12 3v5M12 16v5M3 12h5M16 12h5" stroke="#fff" stroke-width="2"/></svg></div>
  <div class="abs svc left" style="left:84px;top:960px"><h3>Clean/Tune Ups</h3><p>Dust removal, startup cleanup and updates that keep your computer quick and cool.</p><a href="#">READ MORE ›</a></div>
</section>

<section class="why">
  <h2 class="section-title">Why <b>Choose Us</b></h2>
  <div class="abs why-photo" role="img" aria-label="Technician working at a server rack in a bright data room"></div>
  <ul class="abs why-list">
    <li>Certified technicians with years of hands-on experience repairing desktops, laptops and small office networks of every kind.</li>
    <li>Clear, upfront quotes before any work begins, with no hidden fees and no charge if we cannot fix it.</li>
    <li>Same-day service for most repairs, plus on-site visits across the local area for homes and businesses.</li>
    <li>Your privacy matters: we handle every drive and file with care and never look through personal data.</li>
    <li>Every repair is backed by a ninety day warranty on both parts and labour for full peace of mind.</li>
  </ul>
</section>

<section class="help">
  <h2>Just in Case You Need Any Help</h2>
  <div class="abs help-item" style="left:32px"><div class="ring"><svg width="44" height="44" viewBox="0 0 24 24"><rect x="2" y="5" width="20" height="14" fill="#fff"/><path d="M2 5l10 8 10-8" fill="none" stroke="#0b2d66" stroke-width="1.6"/></svg></div><span>EMAIL SUPPORT</span></div>
  <div class="abs help-item" style="left:332px"><div class="ring"><svg width="40" height="44" viewBox="0 0 24 24"><rect x="6" y="2" width="12" height="20" rx="2" fill="none" stroke="#fff" stroke-width="2"/><circle cx="12" cy="18" r="1.2" fill="#fff"/></svg></div><span>FREE PHONE</span></div>
  <div class="abs help-item" style="left:632px"><div class="ring"><svg width="44" height="44" viewBox="0 0 24 24"><path d="M20 7a5 5 0 0 1-6.5 4.8L5 20.3 3.7 19l8.5-8.5A5 5 0 0 1 17 4l-3 3 3 3z" fill="#fff"/></svg></div><span>24/7 SUPPORT</span></div>
  <div class="abs help-item" style="left:932px"><div class="ring">?</div><span>FAQ</span></div>
</section>

<footer class="site-footer">
  <div class="abs footer-brand">KEYPOINT<small>Computer Services</small></div>
  <div class="abs foot-col" style="left:400px"><h4>Important Links</h4><ul><li>Service Area</li><li>Repair Warranty</li><li>Support Hours</li><li>Pricing Guide</li><li>Privacy Policy</li></ul></div>
  <div class="abs foot-col" style="left:680px"><h4>Categories</h4><ul><li>Home Computer Repair</li><li>Small Business IT</li><li>Data Rescue Services</li><li>Network Setup</li></ul></div>
  <div class="abs foot-col" style="left:960px"><h4>Navigation</h4><ul><li>Home</li><li>Services</li><li>About</li><li>Why Us</li><li>Help</li></ul></div>
</footer>

<div class="abs bottom-bar" style="left:0;width:1200px">Copyright 2018 Keypoint Computer Services. All Rights Reserved.
  <div class="abs bottom-social"><span></span><span></span><span></span></div>
</div>

</body>
</html>
```